dsadasdasdasdsa

Industry/Entity Type

Mortgage Broking

Requirements
Must have
• Call-to-action button somewhere on the graphic
Nice to have
• The font of our logo is Montserrat

```html
<!DOCTYPE html>
<html lang="en">
<head>
<meta charset="utf-8">
<title>Mortgage Broker Directory Banner</title>
<link rel="stylesheet" href="https://fonts.googleapis.com/css2?family=Montserrat:wght@400;500;800&display=swap">
<style>
  :root {
    --stage: #3d3b3c;
    --green-top: #22a845;
    --green-bottom: #53bd4a;
    --green-deep: #17783d;
    --green-lime: #8cc63f;
    --ring-grey: #cfcdcd;
    --panel-white: #ffffff;
    --headline-dark: #124a2e;
    --text-light: #ffffff;
    --cta-maroon: #6e1f16;
  }
  * { margin: 0; padding: 0; box-sizing: border-box; }
  html, body {
    width: 1200px;
    height: 1200px;
    overflow: hidden;
    background: var(--stage);
  }
  .banner {
    position: absolute;
    left: 51px;
    top: 517px;
    width: 1097px;
    height: 151px;
    overflow: hidden;
    background: linear-gradient(180deg, var(--green-top), var(--green-bottom));
    box-shadow: 0 6px 18px rgba(0,0,0,0.45);
    font-family: "Montserrat", sans-serif;
  }
  .banner__decor {
    position: absolute;
    inset: 0;
  }
  .banner__mascot {
    position: absolute;
    left: 0;
    top: 0;
    width: 150px;
    height: 151px;
    background: radial-gradient(ellipse at 45% 40%, #7fcf86 0%, #9ed9a0 35%, #e8f4e8 70%, #ffffff 100%),
                linear-gradient(180deg, transparent 70%, #a8643a 100%);
    background-blend-mode: multiply;
  }
  .headline {
    position: absolute;
    right: 444px;
    top: 30px;
    text-align: right;
    line-height: 1;
  }
  .headline__lead {
    display: block;
    color: var(--text-light);
    font-weight: 500;
    font-size: 37px;
    letter-spacing: 0.5px;
  }
  .headline__main {
    display: block;
    margin-top: 8px;
    color: var(--headline-dark);
    font-weight: 800;
    font-size: 38px;
  }
  .divider {
    position: absolute;
    left: 681px;
    top: 17px;
    width: 1.5px;
    height: 115px;
    background: var(--text-light);
  }
  .cta {
    position: absolute;
    left: 709px;
    top: 36px;
    width: 355px;
    height: 80px;
    border-radius: 12px;
    background: var(--cta-maroon);
    color: var(--text-light);
    text-decoration: none;
    font-weight: 500;
    font-size: 22.5px;
    line-height: 34px;
    padding: 6px 0 0 12px;
    white-space: nowrap;
  }
</style>
</head>
<body>
  <div class="banner">
    <svg class="banner__decor" width="1097" height="151" viewBox="0 0 1097 151" aria-hidden="true">
      <polygon points="380,151 530,0 600,0 450,151" fill="#ffffff" opacity="0.05"/>
      <polygon points="520,151 670,0 720,0 570,151" fill="#000000" opacity="0.03"/>
      <polygon points="720,151 870,0 960,0 810,151" fill="#ffffff" opacity="0.05"/>
      <polygon points="920,151 1070,0 1097,0 1097,30 980,151" fill="#000000" opacity="0.04"/>
      <path d="M0,0 H207 Q268,60 252,151 H0 Z" fill="var(--green-deep)"/>
      <path d="M0,0 H170 Q236,52 227,151 H0 Z" fill="var(--green-lime)"/>
      <path d="M0,0 H160 Q224,58 212,151 H0 Z" fill="var(--panel-white)"/>
      <path d="M146,0 Q214,60 199,151" fill="none" stroke="var(--ring-grey)" stroke-width="7"/>
    </svg>
    <div class="banner__mascot" role="img" aria-label="Friendly cartoon turtle mascot smiling toward the viewer"></div>

    <h1 class="headline">
      <span class="headline__lead">Need a</span>
      <span class="headline__main">Mortgage Broker?</span>
    </h1>

    <div class="divider"></div>

    <a class="cta" href="#">Search Now on<br>Australia's Largest Directory</a>
  </div>
</body>
</html>
```